Detail Shop Business card design

i need a business card design for my new detailing company called 'Brisk's Polish Works'. i want an all black and white design . simple, direct and to the point. i want the designer to choose a fitting font to match the logothe front should have logo, address, phone and email and the back side should have a slogan and text indicating that we offer services on anything including cars, trucks, motorcycles and RVs. slogan will read "we take pride in your ride"
maybe also very small on the back side the IG icon with Brisks_Polish_Works

phone 208.417.6352
address 3847 E Larkin Ave
Larkfield ID 83714
email: BrisksPolish@mailvexo.com

Target Market(s)

all ages , auto enthusiasts

Industry/Entity Type

Automotive

Contact Information for Business Card

the front should have logo, address, phone and email and the back side should have a slogan and text indicating that we offer services on anything including cars, trucks, motorcycles and RVs. slogan will read "we take pride in your ride"

phone 208.417.6352
address 3847 E Larkin Ave
Larkfield ID 83714

Colors
000000
ffffff

Requirements
Must have
• bold font and very simple design with good spacing
Nice to have
• anything creative from the designer indicating we service any types of vehicles
Should not have
• any colors ,

```html
<!DOCTYPE html>
<html lang="en">
<head>
<meta charset="utf-8">
<title>Brisk's Polish Works – Business Card</title>
<link href="https://fonts.googleapis.com/css2?family=Oswald:wght@400;600&family=Roboto:wght@400;700;900&display=swap" rel="stylesheet">
<style>
  :root {
    --stage: #ebe8e3;
    --card-front: #ffffff;
    --card-back: #555555;
    --ink: #000000;
    --ink-soft: #2b2b2b;
    --text-grey: #6b6b6b;
    --silhouette: #161616;
  }
  * { margin: 0; padding: 0; box-sizing: border-box; }
  html, body { width: 1200px; height: 950px; overflow: hidden; }
  body { background: var(--stage); position: relative; font-family: "Roboto", Arial, sans-serif; }

  .card {
    position: absolute;
    top: 90px;
    width: 440px;
    height: 770px;
    box-shadow: 0 10px 28px rgba(0,0,0,0.18);
  }

  /* Front */
  .card-front { left: 90px; background: var(--card-front); text-align: center; }
  .brand {
    position: absolute; top: 150px; left: 0; right: 0;
    display: flex; flex-direction: column; align-items: center; gap: 18px;
  }
  .brand-dot { width: 120px; height: 120px; border-radius: 50%; background: var(--ink); }
  .brand-name {
    font-family: "Roboto", Arial, sans-serif; font-weight: 900; font-size: 30px;
    color: var(--ink); text-transform: uppercase; letter-spacing: 1px;
  }
  .star { display: block; margin: 0 auto; }
  .star-single { position: absolute; top: 400px; left: 0; right: 0; }
  .person { position: absolute; top: 428px; left: 0; right: 0; }
  .person-name { font-weight: 700; font-size: 25px; color: var(--ink-soft); letter-spacing: 0.5px; }
  .person-role { font-size: 20px; color: var(--text-grey); margin-top: 2px; }
  .contact { position: absolute; top: 510px; left: 0; right: 0; font-size: 18px; line-height: 25px; color: var(--text-grey); }
  .contact-address { margin-bottom: 18px; }
  .stars-double { position: absolute; top: 690px; left: 0; right: 0; display: flex; justify-content: center; gap: 6px; }

  /* Back */
  .card-back { left: 670px; background: var(--card-back); }
  .message {
    position: absolute; top: 70px; left: 60px; height: 630px;
    writing-mode: vertical-rl;
    display: flex; flex-direction: column; gap: 10px;
  }
  .slogan {
    font-family: "Oswald", Arial, sans-serif; font-weight: 600; font-size: 24px;
    letter-spacing: 1px; color: var(--ink); text-transform: uppercase;
  }
  .slogan-rule { width: 2px; height: 100%; background: var(--ink); }
  .services {
    font-family: "Oswald", Arial, sans-serif; font-weight: 400; font-size: 20px;
    color: var(--ink);
  }
  .vehicle-art {
    position: absolute; top: 80px; left: 175px; width: 210px; height: 600px;
    border-radius: 90px; background: linear-gradient(90deg, var(--silhouette), #2a2a2a);
  }
</style>
</head>
<body>

  <section class="card card-front">
    <div class="brand">
      <span class="brand-dot"></span>
      <span class="brand-name">Brisk's Polish Works</span>
    </div>

    <svg class="star star-single" width="20" height="20" viewBox="0 0 24 24" aria-hidden="true">
      <polygon points="12,1 15,9 23,9 17,14 19,23 12,18 5,23 7,14 1,9 9,9" fill="var(--ink-soft)"/>
    </svg>

    <div class="person">
      <p class="person-name">MARK DALTON</p>
      <p class="person-role">CEO/FOUNDER</p>
    </div>

    <div class="contact">
      <p class="contact-address">3847 E Larkin Ave<br>Larkfield ID 83714</p>
      <p>(P) 208.417.6352</p>
      <p>(M) 208 552 7190</p>
      <p>BrisksPolish@mailvexo.com</p>
      <p>www.briskspolish.com</p>
    </div>

    <div class="stars-double" aria-hidden="true">
      <svg width="18" height="18" viewBox="0 0 24 24"><polygon points="12,1 15,9 23,9 17,14 19,23 12,18 5,23 7,14 1,9 9,9" fill="var(--ink-soft)"/></svg>
      <svg width="18" height="18" viewBox="0 0 24 24"><polygon points="12,1 15,9 23,9 17,14 19,23 12,18 5,23 7,14 1,9 9,9" fill="var(--ink-soft)"/></svg>
    </div>
  </section>

  <section class="card card-back">
    <div class="message">
      <p class="slogan">We take pride in your ride</p>
      <span class="slogan-rule"></span>
      <p class="services">services on anything including cars, trucks, motorcycles &amp; RVs</p>
    </div>
    <div class="vehicle-art" role="img" aria-label="Side silhouette of a classic hot rod car"></div>
  </section>

</body>
</html>
```